Brintel Works - Fast, Efficient and Gas Mainteance for Domestic, Commercial and Industrial clients

We are in the process of purchasing a new business and would like to get a new logo and business card.
Business is a gas maintenance business that also does new gas installations.
Has been established since 1988.
Services include:
Install all types of gas appliances & equipment inc. hot water units
Maintain / repair / replace all types of gas appliances & equipment

Target Market(s)

Domestic, Commercial and Industrial clients

Industry/Entity Type

Business

Contact Information for Business Card

admin@brintelworks.com.au
07 3918 4726
Brintel Works PTY LTD

Logo Text

Gas Fitting & Plumbing Maintenance Specialists

Font styles to use
Sans Serif

Requirements
Must have
• Logo
• Business name, contact number, email address, web address
• Domestic | Commercial | Industrial Est Since 1988
Nice to have
• Possibly a black card with a flame logo to one side
Should not have
• Spelling errors

```html
<!DOCTYPE html>
<html lang="en">
<head>
<meta charset="utf-8">
<title>Brintel Works – Business Card</title>
<link href="https://fonts.googleapis.com/css2?family=Cinzel:wght@700&family=Open+Sans:wght@400;600&family=Great+Vibes&display=swap" rel="stylesheet">
<style>
  :root {
    --page: #ecebe8;
    --orange: #ec6a43;
    --orange-deep: #d9542f;
    --orange-light: #f0825c;
    --white: #ffffff;
    --paper: #f7f7f7;
    --swoosh: #cfcfcf;
    --ink: #4a4a4a;
    --ink-soft: #8a8a8a;
  }
  * { margin: 0; padding: 0; box-sizing: border-box; }
  html, body { width: 1200px; height: 892px; overflow: hidden; background: var(--page); }
  .canvas { position: relative; width: 1200px; height: 892px; }

  .card {
    position: absolute;
    width: 620px; height: 354px;
    border-radius: 22px;
    overflow: hidden;
    box-shadow: 0 10px 26px rgba(0,0,0,.18);
  }
  .card--front { left: 290px; top: 62px; background: var(--paper); }
  .card--back {
    left: 290px; top: 476px;
    background: radial-gradient(ellipse at 35% 40%, var(--orange-light), var(--orange) 55%, var(--orange-deep));
    display: flex; align-items: center; justify-content: center;
  }

  .front-shape { position: absolute; inset: 0; }

  .brand { position: absolute; right: 40px; top: 34px; text-align: left; width: 300px; }
  .brand__name {
    font-family: "Cinzel", serif; font-weight: 700;
    font-size: 30px; color: var(--orange); letter-spacing: .5px; line-height: 1;
  }
  .brand__name small { font-size: 7px; color: var(--ink); vertical-align: top; margin-left: 4px; letter-spacing: .5px; }
  .brand__tagline {
    font-family: "Open Sans", sans-serif; font-weight: 600;
    font-size: 14.5px; color: var(--ink); margin-top: 6px;
  }
  .brand__sectors {
    font-family: "Open Sans", sans-serif; font-size: 8px; color: var(--ink-soft);
    margin-top: 4px; display: flex; align-items: baseline; gap: 10px;
  }
  .brand__est { font-family: "Great Vibes", cursive; font-size: 14px; color: var(--ink-soft); }

  .product-photo {
    position: absolute; left: 40px; bottom: 28px;
    width: 180px; height: 150px; border-radius: 6px;
    background: linear-gradient(160deg, #c9cacc 0%, #9a9b9e 45%, #e0742e 70%, #7a3a1c 100%);
  }

  .contacts {
    position: absolute; right: 40px; bottom: 36px; width: 300px;
    font-family: "Open Sans", sans-serif; color: var(--white);
    font-size: 17px; line-height: 1.45;
  }
  .icons { position: absolute; right: 40px; top: 168px; display: flex; gap: 10px; }
  .icons svg { width: 18px; height: 18px; display: block; }

  .back-name {
    font-family: "Open Sans", sans-serif; font-weight: 600;
    font-size: 46px; color: #f2f2f2; letter-spacing: 1px;
  }
</style>
</head>
<body>
<main class="canvas">

  <section class="card card--front" aria-label="Business card front">
    <svg class="front-shape" viewBox="0 0 620 354" preserveAspectRatio="none" aria-hidden="true">
      <path d="M0 280 C 140 250, 230 130, 380 118 C 470 110, 560 122, 620 132 L620 354 L0 354 Z" fill="var(--swoosh)"/>
      <path d="M0 300 C 150 270, 240 150, 390 138 C 480 130, 560 140, 620 150 L620 354 L0 354 Z" fill="var(--orange)"/>
    </svg>

    <div class="brand">
      <div class="brand__name">BRINTEL WORKS<small>PTY LTD</small></div>
      <div class="brand__tagline">Gas fitting &amp; Plumbing Specialists</div>
      <div class="brand__sectors">
        <span>Domestic | Commercial | Industrial</span>
        <span class="brand__est">Est Since 1988</span>
      </div>
    </div>

    <div class="product-photo" role="img" aria-label="Photo of gas heater and hot water units"></div>

    <div class="icons" aria-hidden="true">
      <svg viewBox="0 0 18 18"><rect width="18" height="18" rx="2" fill="#fff"/><path d="M5 4l2.5 0 1 3-1.5 1a7 7 0 0 0 3 3l1-1.5 3 1 0 2.5c-5 .5-9.5-4-9-9z" fill="var(--orange)"/></svg>
      <svg viewBox="0 0 18 18"><rect width="18" height="18" rx="2" fill="#fff"/><rect x="3.5" y="5" width="11" height="8" fill="none" stroke="var(--orange)" stroke-width="1.4"/><path d="M3.5 5l5.5 4.5 5.5-4.5" fill="none" stroke="var(--orange)" stroke-width="1.4"/></svg>
      <svg viewBox="0 0 18 18"><rect width="18" height="18" rx="2" fill="#fff"/><circle cx="9" cy="9" r="5" fill="none" stroke="var(--orange)" stroke-width="1.4"/><path d="M4 9h10M9 4c-2.5 3-2.5 7 0 10M9 4c2.5 3 2.5 7 0 10" fill="none" stroke="var(--orange)" stroke-width="1"/></svg>
    </div>

    <div class="contacts">
      <div>07 3918 4726</div>
      <div>admin@brintelworks.com.au</div>
      <div>www.brintelworks.com.au</div>
    </div>
  </section>

  <section class="card card--back" aria-label="Business card back">
    <span class="back-name">Brintel Works</span>
  </section>

</main>
</body>
</html>
```